Fitness Equipment & Service

I want to make the card eye catching and fun. We are called Corvane Motion Limited and we are based in Wales. We sell, install and service all types of fitness equipment from Skipping ropes, right through the Dumbbells, Kettle bells and Barbells through to state of the art Treadmills, Running Machines and Strength Equipment. We also design and install changing room furniture and lockers.

TYPOGRAPHY
We would like to use Futrura. Futura has an appearance of efficiency and forwardness. The typeface is derived
from simple geometric forms (near-perfect circles, triangles and squares) and is based on strokes of
near-even weight, which are low in contrast. This is most visible in the almost perfectly round stroke of
the o, which is nonetheless slightly ovoid.
The lowercase has tall ascenders, which rise above the cap line. The uppercase
characters present proportions similar to those of classical Roman capitals.

TYPOGRAPHIC CONSIDERATIONS
No Strike though
No Horizontal Scaling
No Drop Shadows
No Effects
Never use less than 120% Leading

OUR CORPORATE COLOURS
BRAND GUIDELINES
We were thinking that our primary colour palette consists of the Acid Green (Pantone 382) and Process Black.

We work closely with tquarly Ltd and would like to include their name on the card somewhere. I have attached images of the other brands that we work with as an idea or the small icons I have included that illustrate what we do?. I have very kindly been given permission to use any of the images off the files that I have included below, so I hope these help. I will include these below. I would be open to suggestions if it made the card more striking Can you do it?
Updates

Hi All, Just wanted to add a few thoughts but you are the guys with the creative visions (thats why are here) We are based in Wales, UK and we would be open to lots of different ideas on a theme but must be eye catching, Bold and FUN. If you can or think that the Welsh or any dragon could be put in there then go for it (its not a must have) We have also added some ideas for colour but again its over to you!! GO FOR IT ! Thanks and look forward to your visions! Owen

Hi All, Just thought I would sen through the contact details that need to be on the card. (if you want to play around with icons instead of the wording twitter, Facebook, go for it): Corvane Motion Limited Owen Pritchard Managing Director Mob: +44 (0)7582 913 406 e-mail: sales@corvanemotion.co.uk Web: Corvanemotion.co.uk twitter: @motionLetterbin Facebook: Corvane Motion Limited

```html
<!DOCTYPE html>
<html lang="en">
<head>
<meta charset="utf-8">
<title>Corvane Motion Limited — Business Card</title>
<link href="https://fonts.googleapis.com/css2?family=Jost:wght@400;500;600&display=swap" rel="stylesheet">
<style>
  :root {
    --backdrop: #d9d4cb;
    --navy: #15285a;
    --navy-deep: #0f1d45;
    --blue: #1f4a9a;
    --blue-light: #3a64b4;
    --gold: #b8902f;
    --ink: #3b3b3b;
    --paper: #ffffff;
    --paper-shade: #ececec;
    --pale: #c7d3ec;
  }
  * { box-sizing: border-box; margin: 0; padding: 0; }
  html, body { width: 1200px; height: 950px; overflow: hidden; }
  body {
    background: var(--backdrop);
    font-family: "Jost", "Futura", sans-serif;
    position: relative;
  }
  .card {
    position: absolute;
    left: 250px;
    width: 700px;
    height: 400px;
    overflow: hidden;
    box-shadow: 0 6px 18px rgba(0,0,0,0.18);
  }

  /* Front */
  .card-front {
    top: 50px;
    background: linear-gradient(110deg, var(--paper) 55%, var(--paper-shade) 100%);
  }
  .identity { position: absolute; left: 52px; top: 40px; }
  .identity .person-name {
    font-size: 30px; font-weight: 600; color: var(--navy); line-height: 1.2;
  }
  .identity .person-role {
    font-size: 21px; font-weight: 400; color: var(--gold); line-height: 1.2;
  }
  .contact { position: absolute; left: 52px; top: 150px; color: var(--ink); }
  .contact .address { font-size: 19px; line-height: 1.3; margin-bottom: 6px; padding-left: 30px; }
  .contact ul { list-style: none; }
  .contact li {
    display: flex; align-items: center; gap: 10px;
    font-size: 19px; line-height: 1.35;
  }
  .contact .icon { width: 20px; height: 20px; flex: none; }
  .accent-band {
    position: absolute; left: 496px; top: 0; width: 118px; height: 205px;
    background: linear-gradient(180deg, var(--navy-deep) 0%, var(--blue) 70%, var(--blue-light) 100%);
  }
  .brand-mark {
    position: absolute; left: 484px; top: 150px; width: 142px; height: 142px;
  }
  .brand-name {
    position: absolute; left: 420px; top: 310px; width: 270px;
    font-size: 24px; font-weight: 600; color: var(--navy); line-height: 1.2;
    text-align: center;
  }

  /* Back */
  .card-back {
    top: 500px;
    background: linear-gradient(90deg, var(--blue) 0%, var(--navy) 60%, var(--navy-deep) 100%);
  }
  .back-band {
    position: absolute; left: 520px; top: 0; width: 90px; height: 100%;
    background: linear-gradient(90deg, rgba(255,255,255,0) 0%, rgba(170,190,225,0.25) 60%, rgba(255,255,255,0) 100%);
  }
  .back-mark {
    position: absolute; left: 260px; top: 95px; width: 180px; height: 180px;
  }
  .back-web {
    position: absolute; left: 340px; top: 312px;
    display: flex; align-items: center; gap: 12px;
    font-size: 22px; color: var(--pale); line-height: 1.2;
  }
  .back-web .rule { width: 90px; height: 2px; background: var(--pale); opacity: 0.7; }
</style>
</head>
<body>

<section class="card card-front" aria-label="Card front">
  <div class="identity">
    <p class="person-name">Owen Pritchard</p>
    <p class="person-role">Managing Director</p>
  </div>

  <div class="contact">
    <p class="address">27 Harrow Quay Road<br>Penlan, Cardiff CF14 3RT</p>
    <ul>
      <li>
        <svg class="icon" viewBox="0 0 20 20" aria-hidden="true"><rect x="5" y="1" width="10" height="18" rx="2" fill="none" stroke="var(--navy)" stroke-width="2"/><circle cx="10" cy="15.5" r="1.2" fill="var(--navy)"/></svg>
        <span>+44 (0)7582 913 406</span>
      </li>
      <li>
        <svg class="icon" viewBox="0 0 20 20" aria-hidden="true"><rect x="1" y="4" width="18" height="12" fill="var(--navy)"/><path d="M1 4 L10 11 L19 4" fill="none" stroke="#fff" stroke-width="1.5"/></svg>
        <span>sales@corvanemotion.co.uk</span>
      </li>
      <li>
        <svg class="icon" viewBox="0 0 20 20" aria-hidden="true"><circle cx="10" cy="10" r="8.5" fill="var(--navy)"/><ellipse cx="10" cy="10" rx="3.5" ry="8.5" fill="none" stroke="#fff" stroke-width="1.2"/><line x1="1.5" y1="10" x2="18.5" y2="10" stroke="#fff" stroke-width="1.2"/></svg>
        <span>Corvanemotion.co.uk</span>
      </li>
      <li>
        <svg class="icon" viewBox="0 0 20 20" aria-hidden="true"><rect x="2" y="2" width="16" height="16" fill="var(--navy)"/></svg>
        <span>@motionLetterbin</span>
      </li>
      <li>
        <svg class="icon" viewBox="0 0 20 20" aria-hidden="true"><rect x="2" y="2" width="16" height="16" fill="var(--navy)"/></svg>
        <span>Corvane Motion Limited</span>
      </li>
    </ul>
  </div>

  <div class="accent-band"></div>
  <svg class="brand-mark" viewBox="0 0 142 142" aria-hidden="true">
    <circle cx="71" cy="71" r="66" fill="var(--navy)" stroke="#d5d8de" stroke-width="6"/>
  </svg>
  <p class="brand-name">Corvane Motion Limited</p>
</section>

<section class="card card-back" aria-label="Card back">
  <div class="back-band"></div>
  <svg class="back-mark" viewBox="0 0 180 180" aria-hidden="true">
    <circle cx="90" cy="90" r="84" fill="var(--navy-deep)" stroke="#b9c3d6" stroke-width="6"/>
  </svg>
  <div class="back-web">
    <span>Corvanemotion.co.uk</span>
    <span class="rule"></span>
  </div>
</section>

</body>
</html>
```